Business cards and stationary design

We just completed the design of our new logo and we need to print new business cards and letterhead for our nonprofit. We are looking for a fresh new design that shows off our new logo. On letterhead, we must have a column on the right or left to include our Board of Directors (up to 45 names) (see attachment)

Industry/Entity Type

Non-Profit

Contact Information for Business Card

Standard business card with name, title, Company name, mailing address phone numbers, email address and website. Tagline on back "Every neighbor deserves a door"

Font styles to use
Sans Serif

Requirements
Must have
• include pertinent information above
• new logo
• fonts compatible with logo
• should use logo colors only
Nice to have
• tag lines

```html
<!DOCTYPE html>
<html lang="en">
<head>
<meta charset="utf-8">
<title>Shelter Bridge Alliance – Business Card</title>
<link href="https://fonts.googleapis.com/css2?family=Michroma&family=PT+Serif&display=swap" rel="stylesheet">
<style>
  :root {
    --teal: #0a7fa0;
    --red: #e8202a;
    --gold: #f6b530;
    --ink: #333333;
    --paper: #ffffff;
    --cream: #fdf1c8;
    --backdrop: #ece7df;
  }
  * { box-sizing: border-box; margin: 0; padding: 0; }
  html, body {
    width: 1200px; height: 1200px; overflow: hidden;
    background: var(--backdrop);
  }
  .card {
    position: absolute; left: 220px; width: 760px; height: 434px;
    background: var(--paper);
    box-shadow: 0 6px 18px rgba(0,0,0,0.12);
    overflow: hidden;
  }
  .card--front { top: 110px; }
  .card--back {
    top: 656px;
    background: radial-gradient(ellipse at 55% 50%, #ffffff 45%, #fffaf0 70%, var(--cream) 100%);
  }
  .band { position: absolute; inset: 0; }

  .wordmark {
    font-family: "Michroma", sans-serif;
    color: var(--teal);
    letter-spacing: 2px;
    white-space: nowrap;
    display: flex; align-items: center; gap: 12px;
  }
  .wordmark__square { width: 16px; height: 16px; background: var(--gold); display: inline-block; }
  .card--front .wordmark { position: absolute; top: 44px; right: 40px; font-size: 27px; }
  .header-rule { position: absolute; top: 96px; right: 40px; width: 560px; height: 3px; background: var(--red); }

  .contact { position: absolute; left: 360px; top: 138px; color: var(--ink); font-family: "PT Serif", serif; }
  .contact__name {
    font-family: "Michroma", sans-serif; color: var(--red);
    font-size: 17px; letter-spacing: 4px; margin-bottom: 4px;
  }
  .contact__title { font-size: 15px; margin-bottom: 12px; }
  .contact__line { display: flex; align-items: center; gap: 8px; font-size: 15px; line-height: 1.5; }
  .contact__line svg { width: 12px; height: 12px; fill: var(--red); flex: none; }
  .contact__divider { width: 330px; height: 1px; background: var(--red); margin: 8px 0; }

  .card--back .identity {
    position: absolute; left: 50%; top: 50%; transform: translate(-50%, -50%);
    display: flex; flex-direction: column; align-items: center; gap: 22px;
  }
  .card--back .wordmark { font-size: 26px; }
  .tagline {
    font-family: "Michroma", sans-serif; color: var(--red);
    font-size: 15px; letter-spacing: 3px; white-space: nowrap;
  }
</style>
</head>
<body>

<section class="card card--front" aria-label="Business card front">
  <svg class="band" viewBox="0 0 760 434" preserveAspectRatio="none" aria-hidden="true">
    <polygon points="0,200 310,200 310,370 760,370 760,434 0,434" fill="var(--teal)"/>
  </svg>

  <div class="wordmark"><span class="wordmark__square"></span>SHELTER BRIDGE ALLIANCE</div>
  <div class="header-rule"></div>

  <div class="contact">
    <p class="contact__name">MARCUS DELANEY</p>
    <p class="contact__title">Chairman</p>
    <p class="contact__line">
      <svg viewBox="0 0 24 24"><path d="M6.6 10.8a15 15 0 0 0 6.6 6.6l2.2-2.2a1 1 0 0 1 1-.25 11.4 11.4 0 0 0 3.6.57 1 1 0 0 1 1 1V20a1 1 0 0 1-1 1A17 17 0 0 1 3 4a1 1 0 0 1 1-1h3.5a1 1 0 0 1 1 1c0 1.25.2 2.450.57 3.6a1 1 0 0 1-.25 1z"/></svg>
      214.555.0187
    </p>
    <p class="contact__line">
      <svg viewBox="0 0 24 24"><path d="M2 5h20v14H2z M2 5l10 8 10-8"/></svg>
      marcus@sbadallas.org
    </p>
    <p class="contact__line">
      <svg viewBox="0 0 24 24"><circle cx="12" cy="12" r="10"/></svg>
      www.sbadallas.org
    </p>
    <div class="contact__divider"></div>
    <p class="contact__line">
      <svg viewBox="0 0 24 24"><path d="M12 2a7 7 0 0 0-7 7c0 5 7 13 7 13s7-8 7-13a7 7 0 0 0-7-7zm0 9.5a2.5 2.5 0 1 1 0-5 2.5 2.5 0 0 1 0 5z"/></svg>
      P.O Box 20418, Dallas, Texas 75201
    </p>
  </div>
</section>

<section class="card card--back" aria-label="Business card back">
  <div class="identity">
    <div class="wordmark"><span class="wordmark__square"></span>SHELTER BRIDGE ALLIANCE</div>
    <p class="tagline">EVERY NEIGHBOR DESERVES A DOOR</p>
  </div>
</section>

</body>
</html>
```